Residential building / Apartments for sale landing page

I need a website / landing page design for my latest development project - a residential building with 70+ apartments for sale. I need the design in layers in Photoshop/Illustrator/InDesign format with all the icons/shapes/maps/graphic assets in vector format (svg, ai, eps) as much as possible.

I prefer white website and please consider the performance/coding experience. We're not making something suitable only for a design contest with fancy parallax effects and confusing animations. We're trying to create usable and clean UI with good UX.

The website will be custom coded, i.e. I'm not using WordPress.

I know that the existing 3D photos are not good but for now you can use them or replace them with some stock photos. I'm going to create new 3D photos soon.

Real Estate Development

1 page

```html
<!DOCTYPE html>
<html lang="en">
<head>
<meta charset="utf-8">
<title>Tall Grove – Apartments for Sale</title>
<link href="https://fonts.googleapis.com/css2?family=Poppins:wght@300;400;500;600;700&display=swap" rel="stylesheet">
<style>
:root{
  --green:#8dc63f;
  --ink:#1d1d1d;
  --text:#444;
  --muted:#777;
  --light:#f3f3f3;
  --grey:#efefef;
  --white:#fff;
}
*{box-sizing:border-box;margin:0;padding:0}
html,body{width:1200px;height:4435px;overflow:hidden}
body{position:relative;font-family:'Poppins',sans-serif;color:var(--ink);background:var(--white)}
.abs{position:absolute}
/* header */
.brand{left:88px;top:18px;display:flex;align-items:center;gap:10px;font-weight:700;font-size:22px;color:var(--ink);letter-spacing:.5px}
.brand-mark{width:22px;height:22px;background:var(--green);border-radius:50%}
.nav{right:92px;top:28px;display:flex;gap:22px;font-size:11.5px;font-weight:600;text-transform:uppercase}
/* hero */
.hero-img{left:599px;top:69px;width:601px;height:683px;background:linear-gradient(180deg,#cfd9e3 0%,#8a9a7c 30%,#e8ece6 55%,#6f8f4a 100%)}
.hero-arrows{left:553px;top:708px;display:flex}
.hero-arrows span{width:46px;height:44px;display:flex;align-items:center;justify-content:center}
.slides{left:22px;top:380px;font-size:15px;font-weight:600;color:#bbb;line-height:40px}
.slides .on{color:var(--green)}
.slides b{display:inline-block;width:18px;height:2px;background:currentColor;vertical-align:middle;margin-left:4px}
.hero-text{left:107px;top:338px}
.hero-text h2{font-size:29px;font-weight:600;line-height:33px}
.hero-text .big{font-size:60px;font-weight:700;line-height:70px;letter-spacing:1px}
.hero-text .big em{font-style:normal;color:var(--green)}
.hero-text p{font-size:19px;margin-top:0}
.btn{display:inline-block;background:var(--green);color:#fff;font-weight:700;font-size:16px;padding:6px 18px;position:relative}
.btn::after{content:"";position:absolute;left:14px;top:14px;width:100%;height:100%;border-right:1px solid #bbb;border-bottom:1px solid #bbb}
/* project */
.proj-a{left:0;top:857px;width:461px;height:364px;background:linear-gradient(160deg,#e9ecef,#8a7560 60%,#5a6a4a)}
.proj-b{left:310px;top:1042px;width:272px;height:217px;background:linear-gradient(150deg,#e6e1d8,#b7b2a6 60%,#4c5560)}
.proj-text{left:646px;top:985px;width:480px}
.proj-text h3{font-size:25px;font-weight:600;line-height:28px}
.proj-text h2{font-size:46px;font-weight:400;line-height:50px}
.proj-text p{font-size:15px;line-height:25px;color:var(--text);margin-top:10px}
/* section heads */
.head{left:0;width:1200px;text-align:center}
.head h2{font-size:48px;font-weight:400;line-height:54px}
.head p{font-size:15.5px;line-height:25px}
/* facilities */
.cards{left:90px;top:1453px;display:flex;gap:14px}
.card{width:245px;height:282px;background:var(--light);padding:62px 27px 0}
.card.active{background:var(--green);color:#fff;width:234px}
.card h4{font-size:17px;font-weight:600;margin-top:14px}
.card p{font-size:12.5px;line-height:19px;color:var(--muted)}
.card.active p{color:#fff}
.card .more{font-size:11.5px;font-weight:700;margin-top:10px}
.dots{left:590px;top:1772px;display:flex;gap:3px}
.dots i{width:6px;height:6px;background:var(--ink)}
.dots i:first-child{background:var(--green)}
/* construction */
.dark{left:0;top:1854px;width:1200px;height:600px;background:var(--ink);color:#fff}
.features{left:90px;top:2112px;display:grid;grid-template-columns:256px 255px 258px 260px;row-gap:42px}
.feat{padding-left:26px;position:relative;padding-right:12px}
.feat svg{position:absolute;left:0;top:4px}
.feat h4{font-size:17px;font-weight:600;white-space:nowrap;overflow:hidden;text-overflow:ellipsis}
.feat p{font-size:12px;line-height:18px;color:#bbb;margin-top:6px}
/* map */
.map{left:90px;top:2696px;width:1021px;height:413px;background:linear-gradient(135deg,#e9e9e9,#dcdcdc 50%,#ececec)}
.map-pin{left:618px;top:2865px}
/* gallery */
.photo{top:3302px;width:282px;height:370px}
.cap{top:3626px;width:250px;height:81px;background:#fff;text-align:center;padding-top:14px;box-shadow:0 4px 14px rgba(0,0,0,.08)}
.cap h4{font-size:20px;font-weight:500}
.cap span{font-size:13px;font-weight:600;color:var(--green)}
/* contact */
.contact-bg{left:0;top:3826px;width:1200px;height:609px;background:var(--grey)}
.contact h2,.form-title{font-size:46px;font-weight:400;line-height:50px}
.contact{left:86px;top:3960px;width:430px}
.contact p{font-size:15px;line-height:25px;color:var(--text);margin-top:12px}
.info{list-style:none;margin-top:12px;font-size:15.5px;line-height:25px}
.info li{display:flex;align-items:center;gap:10px}
.social{display:flex;gap:8px;margin-top:14px}
.social i{width:26px;height:26px;border-radius:50%;background:var(--ink)}
.form-title{left:598px;top:3960px}
.field{background:#fff;font-size:14px;color:#444;padding:0 22px;display:flex;align-items:center}
.copy{left:0;width:1200px;top:4398px;text-align:center;font-size:15px}
.rule{left:90px;top:4378px;width:1021px;height:1px;background:#d2d2d2}
.totop{left:1122px;top:4364px;width:32px;height:32px;border-radius:50%;background:var(--green);display:flex;align-items:center;justify-content:center}
</style>
</head>
<body>
<header>
  <div class="abs brand"><span class="brand-mark"></span>TALL GROVE</div>
  <nav class="abs nav"><span>Tall Grove</span><span>The Project</span><span>Apartments/Sales</span><span>Location</span><span>Gallery</span><span>Contact</span><span style="text-transform:none;font-weight:500">En ▾</span></nav>
</header>

<section class="hero">
  <div class="abs hero-img" role="img" aria-label="Rendering of a white residential tower with green terraces and a mountain behind"></div>
  <div class="abs hero-arrows">
    <span style="background:var(--ink)"><svg width="12" height="14" viewBox="0 0 12 14"><path d="M8 2 3 7l5 5" stroke="#fff" stroke-width="2" fill="none"/></svg></span>
    <span style="background:var(--green)"><svg width="12" height="14" viewBox="0 0 12 14"><path d="M4 2l5 5-5 5" stroke="#fff" stroke-width="2" fill="none"/></svg></span>
  </div>
  <div class="abs slides"><div class="on">01<b></b></div><div>02<b></b></div><div>03<b></b></div></div>
  <div class="abs hero-text">
    <h2>Sale of apartments directly<br>from the investor with</h2>
    <div class="big"><em>10%</em> DISCOUNT</div>
    <p>Price from XXX EUR/m2</p>
    <a class="btn" style="margin-top:16px">BUY NOW</a>
  </div>
</section>

<section class="project">
  <div class="abs proj-a" role="img" aria-label="Photo of a modern timber and glass building"></div>
  <div class="abs proj-b" role="img" aria-label="Photo of an engineer reviewing building plans"></div>
  <div class="abs proj-text">
    <h3>PROJECT</h3>
    <h2>PRESENTATION</h2>
    <p>Architecture, building materials – facades, roof, common<br>areas etc.), information board (assignor, contractor, etc.),<br>maintenance and management info, level of completion, etc.</p>
  </div>
</section>

<section class="facilities">
  <div class="abs head" style="top:1348px"><h2>FACILITIES / BENEFITS</h2><p style="margin-top:4px">Table with all apartments (70) – unit, floor, entrance/block, typology (1 bed, 2 beds, etc).</p></div>
  <div class="abs cards">
    <div class="card"><svg width="54" height="54" viewBox="0 0 54 54" fill="none" stroke="#1d1d1d" stroke-width="3"><rect x="8" y="18" width="38" height="26" rx="4"/><rect x="20" y="4" width="14" height="12"/><circle cx="16" cy="36" r="3"/><circle cx="38" cy="36" r="3"/></svg><h4>PARKING SPACES</h4><p>Lorem Ipsum is simply dummy text of the printing and typesetting industry.</p><div class="more">READ MORE</div></div>
    <div class="card active"><svg width="70" height="54" viewBox="0 0 70 54" fill="none" stroke="#fff" stroke-width="3"><circle cx="14" cy="38" r="10"/><circle cx="50" cy="38" r="10"/><path d="M14 38l10-16h18l8 16M24 22l6 16"/><rect x="44" y="4" width="14" height="14"/></svg><h4>BICYCLE PARKING</h4><p>Lorem Ipsum is simply dummy text of the printing and typesetting industry.</p><div class="more">READ MORE</div></div>
    <div class="card"><svg width="54" height="54" viewBox="0 0 54 54" fill="none" stroke="#1d1d1d" stroke-width="3"><circle cx="20" cy="10" r="5"/><path d="M8 30l14-10 10 14h14M10 46l30-30"/></svg><h4>RELAXATION AREA</h4><p>Lorem Ipsum is simply dummy text of the printing and typesetting industry.</p><div class="more">READ MORE</div></div>
    <div class="card"><svg width="54" height="54" viewBox="0 0 54 54" fill="none" stroke="#1d1d1d" stroke-width="3"><circle cx="27" cy="27" r="24"/><circle cx="27" cy="27" r="15"/><path d="M22 14v26M32 14v26"/></svg><h4>RESTAURANT</h4><p>Lorem Ipsum is simply dummy text of the printing and typesetting industry.</p><div class="more">READ MORE</div></div>
  </div>
  <div class="abs dots"><i></i><i></i><i></i></div>
</section>

<section class="abs dark"></section>
<div class="abs head" style="top:1972px;color:#fff"><h2>CONSTRUCTION FEATURES</h2><p>Lorem Ipsum is simply dummy text of the printing and typesetting industry.</p></div>
<div class="abs features" style="color:#fff">
  <div class="feat"><svg width="14" height="14"><circle cx="7" cy="7" r="7" fill="#8dc63f"/><path d="M4 7l2 2 4-4" stroke="#fff" stroke-width="1.6" fill="none"/></svg><h4>Norvik Windows</h4><p>5 chamber noise reducing glazing with high temperature and noise insulation efficiency</p></div>
  <div class="feat"><svg width="14" height="14"><circle cx="7" cy="7" r="7" fill="#8dc63f"/><path d="M4 7l2 2 4-4" stroke="#fff" stroke-width="1.6" fill="none"/></svg><h4>Brickhaus bricks</h4><p>Austrian Brickhaus hollow clay bricks with porous system and 25 cm thick outer walls</p></div>
  <div class="feat"><svg width="14" height="14"><circle cx="7" cy="7" r="7" fill="#8dc63f"/><path d="M4 7l2 2 4-4" stroke="#fff" stroke-width="1.6" fill="none"/></svg><h4>High Ceilings</h4><p>2.70m high ceilings giving the light and space you need</p></div>
  <div class="feat"><svg width="14" height="14"><circle cx="7" cy="7" r="7" fill="#8dc63f"/><path d="M4 7l2 2 4-4" stroke="#fff" stroke-width="1.6" fill="none"/></svg><h4>Thermal Insulation System</h4><p>Coatwell Silicone Plaster Thermal Insulation System 10 cm thick and 15 cm thick from the north walls</p></div>
  <div class="feat"><svg width="14" height="14"><circle cx="7" cy="7" r="7" fill="#8dc63f"/><path d="M4 7l2 2 4-4" stroke="#fff" stroke-width="1.6" fill="none"/></svg><h4>Air conditioners</h4><p>All air conditioners piping systems are installed – ready to plug in the inside and outside body of the aircon system</p></div>
  <div class="feat"><svg width="14" height="14"><circle cx="7" cy="7" r="7" fill="#8dc63f"/><path d="M4 7l2 2 4-4" stroke="#fff" stroke-width="1.6" fill="none"/></svg><h4>HPL ventilated facade with</h4><p>Suspended ventilated facade with highly pressed laminated panels by Panelcraft GmbH in wood color</p></div>
  <div class="feat"><svg width="14" height="14"><circle cx="7" cy="7" r="7" fill="#8dc63f"/><path d="M4 7l2 2 4-4" stroke="#fff" stroke-width="1.6" fill="none"/></svg><h4>Panoramic Liftora lifts</h4><p>Giving you the everyday glimpse over the inside garden and putting a smile on your face</p></div>
  <div class="feat"><svg width="14" height="14"><circle cx="7" cy="7" r="7" fill="#8dc63f"/><path d="M4 7l2 2 4-4" stroke="#fff" stroke-width="1.6" fill="none"/></svg><h4>Waterproofing roof</h4><p>PVC membrane with high puncture and tear resistance, UV resistance and vapor permeability</p></div>
</div>

<section class="location">
  <div class="abs head" style="top:2560px"><h2>LOCATION</h2><p>Neighborhood, local attractions, metro/bus stops, schools nearby, big shops etc.<br>Maybe some sort of infographic with distance to the POI above.</p></div>
  <div class="abs map" role="img" aria-label="Street map of the neighbourhood around the building"></div>
  <svg class="abs map-pin" width="26" height="36" viewBox="0 0 26 36"><path d="M13 0C6 0 0 6 0 13c0 9 13 23 13 23s13-14 13-23C26 6 20 0 13 0z" fill="#8dc63f"/><circle cx="13" cy="13" r="5" fill="#fff"/></svg>
</section>

<section class="gallery">
  <div class="abs head" style="top:3203px"><h2>GALLERY</h2><p>boxes for each month with photos of the construction progress</p></div>
  <div class="abs photo" style="left:165px;background:linear-gradient(180deg,#5a9ae0 0%,#a7c8ef 30%,#6a6460 55%,#e8e0d2 100%)" role="img" aria-label="April 2021 construction photo"></div>
  <div class="abs photo" style="left:460px;background:linear-gradient(180deg,#c9cbc6 0%,#9a9d8c 35%,#f0efe9 55%,#5d8a37 100%)" role="img" aria-label="March 2021 construction photo"></div>
  <div class="abs photo" style="left:754px;background:linear-gradient(180deg,#8fc0e6 0%,#e6ecef 40%,#5ec3d6 65%,#6fa24a 100%)" role="img" aria-label="February 2021 construction photo"></div>
  <div class="abs cap" style="left:179px"><h4>April 2021</h4><span>VIEW</span></div>
  <div class="abs cap" style="left:474px"><h4>March 2021</h4><span>VIEW</span></div>
  <div class="abs cap" style="left:768px"><h4>February 2021</h4><span>VIEW</span></div>
</section>

<section class="abs contact-bg"></section>
<div class="abs contact">
  <h2>CONTACT US</h2>
  <p>Contact us for a consultation. Our experts are happy to answer all of your questions and find the best possible solution for the project you are working on.</p>
  <ul class="info">
    <li><svg width="10" height="13" viewBox="0 0 10 13"><path d="M5 0a5 5 0 0 0-5 5c0 4 5 8 5 8s5-4 5-8a5 5 0 0 0-5-5z" fill="#8dc63f"/></svg>Some goes address here</li>
    <li><svg width="12" height="9"><rect width="12" height="9" fill="#8dc63f"/><path d="M0 0l6 5 6-5" stroke="#fff" fill="none"/></svg>info@email.com</li>
    <li><svg width="12" height="12" viewBox="0 0 12 12"><path d="M2 0l3 3-2 2c1 2 2 3 4 4l2-2 3 3-2 2C5 12 0 7 0 2z" fill="#8dc63f"/></svg>+123 4566 8962</li>
  </ul>
  <div class="social"><i></i><i></i><i></i><i></i></div>
</div>
<h2 class="abs form-title">CONTACT FORM</h2>
<div class="abs field" style="left:599px;top:4025px;width:252px;height:40px">Name</div>
<div class="abs field" style="left:860px;top:4025px;width:252px;height:40px">Email</div>
<div class="abs field" style="left:599px;top:4073px;width:513px;height:40px">Phone number</div>
<div class="abs field" style="left:599px;top:4122px;width:513px;height:108px;align-items:flex-start;padding-top:12px">Message</div>
<a class="abs btn" style="left:599px;top:4241px;width:122px;height:32px;font-size:14px;text-align:center;padding:6px 0">SUBMIT</a>

<div class="abs rule"></div>
<div class="abs copy">Copyright 2021 | All Rights Reserved</div>
<div class="abs totop"><svg width="12" height="8" viewBox="0 0 12 8"><path d="M1 7l5-5 5 5" stroke="#fff" stroke-width="2" fill="none"/></svg></div>
</body>
</html>
```